Business Card Design

I need a business card for a new company based in Australia called "MedLinkora".

Its a cloud program for GPs that allows them to search for the specialist they require using a simple user friendly tool.

I would like the colours to match those in the program (the colours in the logo attached).

The final design should reflect the programs clarity, ease of use and professionalism.

Target Market(s)

GPs and other Health Professionals

Industry/Entity Type

Business

Contact Information for Business Card

MedLinkora; The Whole Consultant Index; Marla Voss CEO; 0438215967; marla@medlinkora.example; www.medlinkora.example

Requirements
Must have
• Must have the logo attached; the web address and my name and phone number
Nice to have
• the slogan "The Whole Consultant Index"

```html
<!DOCTYPE html>
<html lang="en">
<head>
<meta charset="utf-8">
<title>MedLinkora Business Card</title>
<link href="https://fonts.googleapis.com/css2?family=Open+Sans:wght@400;600;700&display=swap" rel="stylesheet">
<style>
  :root {
    --cyan: #1fb3e0;
    --grey-bar: #9b9d9f;
    --ink: #3a3a3a;
    --muted: #8a8a8a;
    --card: #ffffff;
    --backdrop: #e9e7e3;
  }
  * { box-sizing: border-box; margin: 0; padding: 0; }
  html, body { width: 1200px; height: 829px; overflow: hidden; }
  body {
    background: var(--backdrop);
    font-family: "Open Sans", Arial, sans-serif;
    position: relative;
  }
  .card {
    position: absolute;
    width: 520px;
    height: 300px;
    background: var(--card);
    box-shadow: 0 2px 6px rgba(0,0,0,0.15);
    overflow: hidden;
  }
  .card--front { left: 50px; top: 265px; }
  .card--back { left: 630px; top: 265px; }

  .brand { color: var(--cyan); font-weight: 600; letter-spacing: -0.5px; line-height: 1; }
  .tagline { color: var(--muted); font-weight: 400; line-height: 1; }

  /* Front */
  .front__brand { position: absolute; right: 30px; top: 30px; text-align: left; }
  .front__brand .brand { font-size: 40px; }
  .front__brand .tagline { font-size: 12.5px; margin-top: 4px; }

  .front__grey-block { position: absolute; right: 0; top: 112px; width: 82px; height: 18px; background: var(--grey-bar); }
  .front__band { position: absolute; left: 190px; right: 82px; top: 124px; height: 10px; background: var(--cyan); }

  .front__accent { position: absolute; left: 0; top: 100px; width: 10px; height: 44px; background: var(--cyan); }
  .front__name { position: absolute; left: 28px; top: 98px; font-size: 20px; font-weight: 700; color: var(--cyan); }
  .front__role { position: absolute; left: 28px; top: 124px; font-size: 14px; color: var(--muted); }

  .contacts { position: absolute; left: 28px; top: 196px; list-style: none; }
  .contacts li { display: flex; align-items: center; gap: 10px; font-size: 15px; color: var(--ink); height: 26px; }
  .contacts svg { width: 16px; height: 16px; flex: none; }

  /* Back */
  .back__brand { position: absolute; left: 0; right: 0; top: 92px; text-align: center; }
  .back__brand .brand { font-size: 58px; }
  .back__brand .tagline { font-size: 17px; margin-top: 6px; }
  .back__web { position: absolute; left: 0; right: 0; top: 218px; text-align: center; font-size: 20px; color: var(--ink); letter-spacing: 0.5px; }
</style>
</head>
<body>

<section class="card card--front" aria-label="Business card front">
  <div class="front__brand">
    <div class="brand">MedLinkora</div>
    <div class="tagline">The Whole Consultant Index</div>
  </div>
  <div class="front__grey-block"></div>
  <div class="front__band"></div>
  <div class="front__accent"></div>
  <div class="front__name">Marla Voss</div>
  <div class="front__role">CEO</div>
  <ul class="contacts">
    <li>
      <svg viewBox="0 0 16 16" aria-hidden="true"><circle cx="8" cy="8" r="8" fill="var(--cyan)"/><path d="M5.5 4.2c.4-.3.9-.2 1.1.2l.7 1.3c.2.4.1.8-.2 1l-.5.4c.4.9 1.1 1.7 2 2.2l.4-.5c.3-.3.7-.4 1-.2l1.3.7c.4.2.5.7.2 1.1l-.5.7c-.4.5-1.1.6-1.7.3C7.4 10.4 5.6 8.6 4.6 6.7c-.3-.6-.2-1.3.3-1.7z" fill="#fff"/></svg>
      0438215967
    </li>
    <li>
      <svg viewBox="0 0 16 16" aria-hidden="true"><circle cx="8" cy="8" r="8" fill="var(--cyan)"/><rect x="4" y="5.2" width="8" height="5.6" rx="0.6" fill="#fff"/><path d="M4.3 5.6 8 8.4l3.7-2.8" stroke="var(--cyan)" stroke-width="0.9" fill="none"/></svg>
      marla@medlinkora.example
    </li>
    <li>
      <svg viewBox="0 0 16 16" aria-hidden="true"><circle cx="8" cy="8" r="8" fill="var(--cyan)"/><g stroke="#fff" stroke-width="0.9" fill="none"><circle cx="8" cy="8" r="4.2"/><ellipse cx="8" cy="8" rx="1.8" ry="4.2"/><path d="M3.8 8h8.4"/></g></svg>
      www.medlinkora.example
    </li>
  </ul>
</section>

<section class="card card--back" aria-label="Business card back">
  <div class="back__brand">
    <div class="brand">MedLinkora</div>
    <div class="tagline">The Whole Consultant Index</div>
  </div>
  <div class="back__web">www.medlinkora.example</div>
</section>

</body>
</html>
```